Business Card Design & Gift cards, Gift Cert, Donation Card

Retail Gift Store-in addition to Business Cards we'd like sequenced 2 sided Gift cards, Gift Certificate Cards, and Donation Cards.please see examples and email for clarificationlogos attached with examples-
Gift Card, Gift Certificate and Donation Card will all be same style just differant upper right title, with back side info as example.
business card, as example is single sided.
looking for additional ideas for layout

Industry/Entity Type

Business

Contact Information for Business Card

211 Newman St.East Tawas, MI 48730989.362.8730Office@BrewKrew.com

Requirements
Must have
• Blue as per example
• Logos provided
• like gradiant background

```html
<!DOCTYPE html>
<html lang="en">
<head>
<meta charset="utf-8">
<title>Tillow Marsh – Business Card &amp; Gift Card</title>
<link rel="stylesheet" href="https://fonts.googleapis.com/css2?family=Comic+Neue:wght@400;700&family=Roboto:wght@400&display=swap">
<style>
  :root {
    --backdrop: #5a5a5a;
    --card: #ffffff;
    --ink: #111111;
    --panel: #000000;
    --panel-text: #ffffff;
    --rule: #333333;
    --mark-blue: #dfe6f7;
    --mark-sun: #fbf5d2;
  }
  * { margin: 0; padding: 0; box-sizing: border-box; }
  html, body { width: 1105px; height: 1200px; overflow: hidden; }
  body {
    background: var(--backdrop);
    position: relative;
    font-family: "Comic Neue", "Comic Sans MS", cursive;
    color: var(--ink);
  }
  .card {
    position: absolute;
    left: 196px;
    width: 720px;
    height: 413px;
    background: var(--card);
    border-radius: 22px;
    overflow: hidden;
  }
  .card--front { top: 145px; }
  .card--back { top: 602px; }

  .contact-panel {
    position: absolute;
    left: 0; top: 0;
    width: 343px; height: 100%;
    background: var(--panel);
    color: var(--panel-text);
    border-radius: 0 36px 36px 0;
    padding: 60px 0 0 44px;
    font-size: 21px;
    line-height: 28px;
  }
  .contact-panel p { white-space: nowrap; }
  .address { margin-bottom: 12px; }
  .contact-line { display: flex; align-items: center; gap: 10px; height: 30px; }
  .contact-line svg { width: 17px; height: 17px; flex: none; }
  .offerings { margin-top: 12px; line-height: 30px; }

  .brand-name {
    position: absolute;
    left: 343px; right: 0;
    top: 168px;
    text-align: center;
    font-size: 50px;
    font-weight: 400;
    letter-spacing: 1px;
    color: var(--ink);
  }

  .card-number {
    position: absolute;
    right: 40px; top: 36px;
    font-family: "Roboto", Arial, sans-serif;
    font-size: 19px;
  }
  .mark-area {
    position: absolute;
    left: 232px; top: 33px;
    width: 325px; height: 352px;
    border-radius: 40% 40% 20% 20%;
    background: linear-gradient(180deg, var(--mark-blue) 0%, var(--mark-blue) 55%, var(--mark-sun) 100%);
    opacity: 0.8;
  }
  .field {
    position: absolute;
    display: flex;
    align-items: baseline;
    white-space: nowrap;
  }
  .field .rule {
    flex: 1;
    border-bottom: 1.5px solid var(--rule);
    margin-left: 14px;
    transform: translateY(-4px);
  }
  .field--large { font-size: 27px; left: 57px; }
  .field--small { font-size: 22px; left: 55px; }
</style>
</head>
<body>
  <section class="card card--front" aria-label="Business card">
    <div class="contact-panel">
      <p class="address">482 Larkfield Ave.<br>Harlow Bay, MI 48921</p>
      <p class="contact-line">
        <svg viewBox="0 0 16 16" aria-hidden="true"><path fill="#fff" d="M3.5 1.5l2.4 0 1.1 3.4-1.6 1.3c.9 1.9 2.4 3.4 4.3 4.3l1.3-1.6 3.4 1.1 0 2.4c0 .8-.7 1.6-1.6 1.6C7.4 14 2 8.6 2 3.1c0-.9.7-1.6 1.5-1.6z"/></svg>
        989.517.4296
      </p>
      <p class="contact-line">
        <svg viewBox="0 0 16 16" aria-hidden="true"><rect x="1.5" y="3.5" width="13" height="9" fill="#fff"/><path d="M1.5 3.5l6.5 5 6.5-5" fill="none" stroke="#000" stroke-width="1.3"/></svg>
        Office@TillowMarsh.com
      </p>
      <p class="contact-line">
        <svg viewBox="0 0 16 16" aria-hidden="true"><circle cx="8" cy="8" r="6.5" fill="#fff"/><path d="M4 5.5c1.5 0 2 1 3 1.5s0 2 1 2.5 1 2 0 3M10 3.5c0 1.5 1.5 1.5 2.5 2M9.5 10c1-.5 2 0 3-1" fill="none" stroke="#000" stroke-width="1.2"/></svg>
        www.TillowMarsh.com
      </p>
      <p class="offerings">Gourmet Food<br>Fine Wines | Gift Baskets<br>Kitchen &amp; Bath Accessories<br>Candles | Cards | Soaps</p>
    </div>
    <h1 class="brand-name">TILLOW MARSH</h1>
  </section>

  <section class="card card--back" aria-label="Gift card back">
    <div class="mark-area" role="img" aria-label="Faint brand illustration of a dancing figure over a rising sun"></div>
    <p class="card-number">Card Number : 58724</p>
    <div class="field field--large" style="top:78px; width:610px;"><span>To :</span><span class="rule"></span></div>
    <div class="field field--large" style="top:136px; width:610px;"><span>Form :</span><span class="rule"></span></div>
    <div class="field field--small" style="top:218px; width:619px;"><span>Date&nbsp; Issued :</span><span class="rule" style="margin-left:4px"></span></div>
    <div class="field field--small" style="top:267px; width:619px;"><span>Expiration Date :</span><span class="rule" style="margin-left:4px"></span></div>
    <div class="field field--small" style="top:315px; width:619px;"><span>Employee :</span><span class="rule" style="margin-left:22px"></span></div>
  </section>
</body>
</html>
```